Make a great menu for our Seafood Restaurant MarLo

Design a iconic menu for my fish restaurant on the island of Phu Quoc, Vietnam. Coastal, seafood and pictures of all menu items inside. For our restaurant menu help us transform our food photos and some saucy sentences into a complete, professional restaurant menu.

A logo is in the works, leave empty space, colors will be mostly blue on lots of white, not all dishes have to be in the menu but most should be in there.

Should be a classy menu, not to busy looking.

Ive attached two samples. Attached also all images.

Target Market(s)

Mostly Asian guests

Industry/Entity Type

Seafood Restaurant

Font styles to use
Sans Serif
Decorative
Script

Colors
3176b5
33a6d7
0692cd
0255a3
85abd2
85cae6
ecf7fb
cfdeed
ffffff

Requirements
Must have
• Sazz, lots of pictures, cool menu, playfull and cheeky, but still classy if this makes any sense.
• Size of menu probably half A3, like 25CM wide by 36 CM high

```html
<!DOCTYPE html>
<html lang="en">
<head>
<meta charset="utf-8">
<title>MarLo Seafood Menu – Healthy Choices</title>
<link href="https://fonts.googleapis.com/css2?family=Quicksand:wght@500;600&family=Yellowtail&family=Marcellus&family=Crimson+Text:wght@400;600&display=swap" rel="stylesheet">
<style>
  :root {
    --backdrop: #dfe6ea;
    --paper: #ffffff;
    --wash: #cfdeed;
    --wash-light: #ecf7fb;
    --wash-mid: #85cae6;
    --brand-teal: #7fbfae;
    --blue-bright: #33a6d7;
    --blue-deep: #0255a3;
    --blue-mid: #3176b5;
    --ink: #2b2f33;
    --plate: #efe9dd;
    --sketch: #9aa0a5;
  }
  * { box-sizing: border-box; margin: 0; padding: 0; }
  html, body { width: 1200px; height: 1200px; overflow: hidden; }
  body {
    background: var(--backdrop);
    display: flex; align-items: center; justify-content: center;
    font-family: "Crimson Text", Georgia, serif;
    color: var(--ink);
  }
  .spread {
    display: flex; width: 1100px; height: 790px;
    box-shadow: 0 18px 40px rgba(40, 60, 80, 0.18);
  }
  .page {
    position: relative; width: 550px; height: 790px;
    background: var(--paper); overflow: hidden;
  }
  .page--left { border-right: 1px solid #e4eaee; }
  .wash {
    position: absolute; inset: 0 0 auto 0; height: 62%;
    background:
      radial-gradient(ellipse 70% 55% at 40% 20%, var(--wash) 0%, rgba(207,222,237,0.6) 45%, transparent 75%),
      radial-gradient(ellipse 60% 45% at 80% 45%, var(--wash-light) 0%, transparent 70%),
      linear-gradient(180deg, #d6e6f2 0%, var(--wash-light) 60%, var(--paper) 100%);
  }
  .page--right .wash { height: 55%; }

  .brand-name {
    position: absolute; top: 170px; left: 60px;
    font-family: "Quicksand", sans-serif; font-weight: 600;
    font-size: 96px; letter-spacing: 2px; color: var(--brand-teal);
  }
  .intro {
    position: absolute; top: 340px; left: 60px; width: 430px;
    font-size: 15px; line-height: 1.45;
  }
  .intro p + p { margin-top: 10px; }
  .coast-sketch {
    position: absolute; left: 0; right: 0; bottom: 0; height: 300px;
    background: linear-gradient(180deg, #ffffff 0%, #eef0f2 40%, #c9cdd1 100%);
  }

  .section-title { position: absolute; top: 40px; left: 50px; }
  .section-title .script {
    font-family: "Yellowtail", cursive; font-size: 72px;
    color: var(--blue-bright); line-height: 1;
  }
  .section-title .caps {
    display: block; margin: -14px 0 0 56px;
    font-family: "Quicksand", sans-serif; font-weight: 500;
    font-size: 16px; letter-spacing: 6px; color: var(--blue-bright);
  }

  .dish { position: absolute; }
  .dish__photo {
    border-radius: 50%;
    background: radial-gradient(ellipse at center, #c9a770 0%, #d9c79e 38%, var(--plate) 62%, #f7f3ea 100%);
    box-shadow: 0 8px 16px rgba(60, 70, 80, 0.18);
  }
  .dish__name {
    margin-top: 10px;
    font-family: "Marcellus", serif; font-size: 15px;
    letter-spacing: 1px; text-transform: uppercase; color: var(--blue-bright);
  }
  .dish__name .price { font-size: 11px; margin-left: 4px; }
  .dish__desc { font-size: 13px; line-height: 1.3; }
  .dish__tag { font-size: 11px; letter-spacing: 1px; }

  .dish--snapper { top: 150px; left: 190px; width: 330px; }
  .dish--snapper .dish__photo { width: 330px; height: 180px; }
  .dish--oysters { top: 400px; left: 40px; width: 220px; }
  .dish--oysters .dish__photo { width: 200px; height: 120px; }
  .dish--herring { top: 400px; left: 300px; width: 220px; }
  .dish--herring .dish__photo { width: 200px; height: 120px;
    background: radial-gradient(ellipse at center, #d98a7a 0%, #e7c6b3 35%, var(--plate) 62%, #f7f3ea 100%); }
  .dish--rolls { top: 590px; left: 40px; width: 220px; }
  .dish--rolls .dish__photo { width: 200px; height: 120px;
    background: radial-gradient(ellipse at center, #e9b48c 0%, #dfe3c9 38%, var(--plate) 62%, #f7f3ea 100%); }
  .dish--salad { top: 590px; left: 300px; width: 220px; }
  .dish--salad .dish__photo { width: 200px; height: 120px;
    background: radial-gradient(ellipse at center, #a8c66c 0%, #dbe2b5 38%, var(--plate) 62%, #f7f3ea 100%); }
</style>
</head>
<body>
  <main class="spread">
    <section class="page page--left">
      <div class="wash"></div>
      <h1 class="brand-name">MarLo</h1>
      <div class="intro">
        <p>At our seafood restaurant we will serve you an eclectic mix of Phu Quoc flavours, all fresh from the sea, the menu with gorgeous pictures and Fusion dishes highlighted as healthy specials.</p>
        <p>Instead of the traditional menu starter, main or dessert you will see our menu set up in a relaxed family style friendly way as people like to eat in Phu Quoc.</p>
        <p>From our menu you will be able to choose from our wok, grill, raw, smoke, steam, fried and more, and be able to combine these dishes into a big family style platter.</p>
      </div>
      <div class="coast-sketch" role="img" aria-label="Pencil sketch of a Phu Quoc fishing beach with round basket boats, palms and hills"></div>
    </section>

    <section class="page page--right">
      <div class="wash"></div>
      <header class="section-title">
        <span class="script">Lina's</span>
        <span class="caps">HEALTHY CHOICES</span>
      </header>

      <article class="dish dish--snapper">
        <div class="dish__photo" role="img" aria-label="Photo of poached red snapper on spinach bulgur with prawn"></div>
        <h2 class="dish__name">Poached Red Snapper<span class="price">100</span></h2>
        <p class="dish__desc">Spinach bulgur mixed with sous-vide prawn tartar, saffron foam</p>
        <p class="dish__tag">GF</p>
      </article>

      <article class="dish dish--oysters">
        <div class="dish__photo" role="img" aria-label="Photo of fresh oysters on ice with lime"></div>
        <h2 class="dish__name">Vietnamese Oysters<span class="price">100</span></h2>
        <p class="dish__desc">½ dozen, served on ice with Phu Quoc black pepper and lime</p>
        <p class="dish__tag">GF</p>
      </article>

      <article class="dish dish--herring">
        <div class="dish__photo" role="img" aria-label="Photo of herring salad with herbs on rice paper"></div>
        <h2 class="dish__name">Goi Ca Trich<span class="price">100</span></h2>
        <p class="dish__desc">Phu Quoc Herring with Salad, Herbs and Rice Paper as a single dish or sharing</p>
        <p class="dish__tag">GF</p>
      </article>

      <article class="dish dish--rolls">
        <div class="dish__photo" role="img" aria-label="Photo of fresh spring rolls with dipping sauce"></div>
        <h2 class="dish__name">A Delicious Mix of Our Fresh Spring Rolls<span class="price">100</span></h2>
        <p class="dish__desc">Fish cake, shrimps, roasted duck, Phu Quoc crab</p>
        <p class="dish__tag">GF</p>
      </article>

      <article class="dish dish--salad">
        <div class="dish__photo" role="img" aria-label="Photo of green mango seafood salad"></div>
        <h2 class="dish__name">Green Mango Salad<span class="price">100</span></h2>
        <p class="dish__desc">Squid, herbs, lime and roasted peanuts</p>
        <p class="dish__tag">GF</p>
      </article>
    </section>
  </main>
</body>
</html>
```